Business Card Design for ReaL ESTATE AGENT

New Business Cards for a real estate agent in Jacksonville, FL. My specialty is urban core, historic districts but sell through out the city. Company Name is Ninth and Crest Realty a division of the Dunholt Companies. The card needs to convey an essence of professionalism, knowledge and success.

Target Market(s)

Home buyers and Sellers

Industry/Entity Type

Real Estate

Contact Information for Business Card

Double sided

Font styles to use
Sans Serif

Requirements
Must have
• My logs and photo (provided). My contact information as follows:
• Owen Talbrick
• Cell 904-555-0183
• Office 904-555-0147
• Email owentalbrick@mailbrook.example
Nice to have
• Tag Line - Exceptional Effort. Proven Results.

```html
<!DOCTYPE html>
<html lang="en">
<head>
<meta charset="utf-8">
<title>Ninth and Crest Realty – Business Card</title>
<link href="https://fonts.googleapis.com/css2?family=Open+Sans:wght@400;600;700&display=swap" rel="stylesheet">
<style>
  :root {
    --backdrop: #8e8d8a;
    --card-black: #000000;
    --band-dark: #121212;
    --coral: #e8543f;
    --forest: #1f5a3e;
    --white: #ffffff;
    --photo-light: #6b6e73;
    --photo-dark: #1d1f24;
  }
  * { margin: 0; padding: 0; box-sizing: border-box; }
  html, body {
    width: 1200px; height: 900px; overflow: hidden;
    background: var(--backdrop);
    font-family: "Open Sans", Arial, sans-serif;
  }
  .canvas { position: relative; width: 1200px; height: 900px; }

  .card {
    position: absolute; left: 280px;
    width: 640px; height: 366px;
    background: var(--card-black);
    overflow: hidden;
    box-shadow: 0 6px 18px rgba(0,0,0,.35);
  }
  .card--front { top: 62px; }
  .card--back  { top: 472px; }

  .stripes { position: absolute; left: 0; right: 0; bottom: 0; }
  .stripes__green { height: 8px; background: var(--forest); }
  .stripes__coral { height: 26px; background: var(--coral); }

  /* Front: brand */
  .brand {
    position: absolute; left: 0; right: 0; top: 92px;
    display: flex; align-items: center; justify-content: center; gap: 22px;
  }
  .brand__mark { width: 70px; height: 70px; background: var(--forest); }
  .brand__name {
    color: var(--coral);
    font-weight: 700; font-size: 38px; line-height: 1.12;
    text-transform: uppercase; letter-spacing: 1px;
  }

  /* Back: agent */
  .portrait {
    position: absolute; left: 0; top: 20px;
    width: 290px; height: 228px;
    background: radial-gradient(ellipse at 55% 35%, var(--photo-light), var(--photo-dark) 75%);
  }
  .agent { position: absolute; right: 44px; top: 118px; text-align: right; }
  .agent__name {
    color: var(--coral); font-weight: 600; font-size: 17px;
    text-transform: uppercase; letter-spacing: .3px;
  }
  .agent__title { color: var(--white); font-size: 15px; margin-top: 2px; }

  .contact-band {
    position: absolute; left: 0; right: 0; top: 248px; bottom: 34px;
    background: var(--band-dark);
  }
  .contact {
    position: absolute; color: var(--white); font-size: 15px;
    display: flex; align-items: center; gap: 6px; white-space: nowrap;
  }
  .contact--phone { left: 46px; top: 8px; }
  .contact--email { right: 44px; bottom: 10px; }
  .contact__label { color: var(--coral); font-weight: 600; }
  .contact__sep { margin: 0 6px; color: var(--coral); }
  .contact svg { width: 13px; height: 13px; fill: var(--coral); }
</style>
</head>
<body>
<div class="canvas">

  <section class="card card--front" aria-label="Card front">
    <div class="brand">
      <div class="brand__mark"></div>
      <div class="brand__name">Ninth and Crest<br>Realty</div>
    </div>
    <div class="stripes">
      <div class="stripes__green"></div>
      <div class="stripes__coral"></div>
    </div>
  </section>

  <section class="card card--back" aria-label="Card back">
    <div class="portrait" role="img" aria-label="Portrait photo of the agent in a dark suit and red tie"></div>
    <div class="agent">
      <div class="agent__name">Owen Talbrick</div>
      <div class="agent__title">Managing Director</div>
    </div>
    <div class="contact-band">
      <div class="contact contact--phone">
        <svg viewBox="0 0 16 16" aria-hidden="true"><path d="M3 1h3l1.5 4-2 1.3a9 9 0 0 0 4.2 4.2L11 8.5l4 1.5v3a2 2 0 0 1-2 2A12 12 0 0 1 1 3a2 2 0 0 1 2-2z"/></svg>
        <span><span class="contact__label">C</span> 904-555-0183<span class="contact__sep">|</span><span class="contact__label">O</span> 904-555-0147</span>
      </div>
      <div class="contact contact--email">
        owentalbrick@mailbrook.example
        <svg viewBox="0 0 16 16" aria-hidden="true"><path d="M1 3h14v10H1z M1.5 3.5 8 9l6.5-5.5" stroke="#121212" stroke-width="1.2"/></svg>
      </div>
    </div>
    <div class="stripes">
      <div class="stripes__green"></div>
      <div class="stripes__coral"></div>
    </div>
  </section>

</div>
</body>
</html>
```